Harbor Crestline (Business Card Design)

Need business cards designed. Something modern, chic, and sleek. Mabye the back of the card should be the navy blue that is in the logo and then just the logo on the back.

Target Market(s)

Those in the hotel, office, and renovation industry

Contact Information for Business Card

1. Logo 2. Dorian Fenwick 3. CEO/Founder 4. Phone: (833) HarbCre / (833) 427-2731 5. Email: dorian@theharborcrestline.com 6. Website: www.theharborcrestline.com

Font styles to use
Other font styles liked:
• Look at the logo font and base the font for everything else off of that.

Colors
0054AA
0677BA
7BADD7
CADEEF
E8F1F8

Requirements
Must have
• Colors that are associated in the logo
Nice to have
• Sleek modern clean and chic design.

```html
<!DOCTYPE html>
<html lang="en">
<head>
<meta charset="utf-8">
<title>Harbor Crestline — Business Card</title>
<link rel="stylesheet" href="https://fonts.googleapis.com/css2?family=Poppins:wght@400;500;600&display=swap">
<style>
  :root {
    --backdrop: #8a8a8a;
    --card-white: #ffffff;
    --navy: #0c1a43;
    --navy-deep: #0b1941;
    --gold: #c9a14a;
    --ink: #15182a;
    --divider: #c4c6cc;
    --emboss-blue: #2a4bb3;
  }
  * { margin: 0; padding: 0; box-sizing: border-box; }
  html, body {
    width: 1093px; height: 1200px; overflow: hidden;
    background: var(--backdrop);
    font-family: "Poppins", sans-serif;
  }
  .canvas { position: relative; width: 1093px; height: 1200px; }

  .card {
    position: absolute; left: 265px; width: 578px; height: 356px;
    border-radius: 24px;
    box-shadow: 3px 4px 4px rgba(0,0,0,0.55);
  }
  .card--front { top: 226px; background: var(--card-white); }
  .card--back { top: 621px; background: var(--navy-deep); }

  .brand {
    position: absolute; display: flex; flex-direction: column; align-items: center;
  }
  .brand__mark { width: 12px; height: 12px; background: var(--gold); margin-bottom: 14px; }
  .brand__name {
    font-weight: 600; letter-spacing: 0.5px; white-space: nowrap;
  }
  .card--front .brand { left: 0; width: 221px; top: 152px; }
  .card--front .brand__name { color: var(--navy); font-size: 21px; }

  .card--back .brand { left: 0; width: 100%; top: 150px; }
  .card--back .brand__mark { background: var(--emboss-blue); width: 14px; height: 14px; margin-bottom: 16px; }
  .card--back .brand__name { color: var(--emboss-blue); font-size: 28px; }

  .divider {
    position: absolute; left: 220px; top: 74px; width: 1.5px; height: 209px;
    background: linear-gradient(to bottom, rgba(196,198,204,0), var(--divider) 20%, var(--divider) 80%, rgba(196,198,204,0));
  }

  .person { position: absolute; left: 243px; top: 100px; }
  .person__name { color: var(--navy); font-size: 23px; font-weight: 600; line-height: 1.1; letter-spacing: -0.2px; }
  .person__title { color: var(--gold); font-size: 14px; font-weight: 400; line-height: 1.2; margin-top: 2px; }

  .contacts { position: absolute; left: 243px; top: 179px; list-style: none; }
  .contacts__item {
    display: flex; align-items: center; gap: 7px;
    color: var(--ink); font-size: 17px; line-height: 24.5px; white-space: nowrap;
  }
  .contacts__icon { width: 15px; height: 15px; flex: none; fill: var(--navy); }
</style>
</head>
<body>
<main class="canvas">
  <section class="card card--front" aria-label="Business card front">
    <div class="brand">
      <span class="brand__mark"></span>
      <span class="brand__name">Harbor Crestline</span>
    </div>
    <div class="divider"></div>
    <div class="person">
      <h1 class="person__name">DORIAN FENWICK</h1>
      <p class="person__title">CEO/FOUNDER</p>
    </div>
    <ul class="contacts">
      <li class="contacts__item">
        <svg class="contacts__icon" viewBox="0 0 24 24" aria-hidden="true"><path d="M6.6 10.8a15.5 15.5 0 0 0 6.6 6.6l2.2-2.2a1 1 0 0 1 1-.25 11.4 11.4 0 0 0 3.6.57 1 1 0 0 1 1 1V20a1 1 0 0 1-1 1A17 17 0 0 1 3 4a1 1 0 0 1 1-1h3.5a1 1 0 0 1 1 1c0 1.25.2 2.45.57 3.57a1 1 0 0 1-.25 1z"/></svg>
        (833) HarbCre / (833) 427-2731
      </li>
      <li class="contacts__item">
        <svg class="contacts__icon" viewBox="0 0 24 24" aria-hidden="true"><path d="M2 5h20v14H2z M3.5 6.5 12 13l8.5-6.5" fill="var(--navy)" stroke="#fff" stroke-width="1.4"/></svg>
        dorian@theharborcrestline.com
      </li>
      <li class="contacts__item">
        <svg class="contacts__icon" viewBox="0 0 24 24" aria-hidden="true" fill="none" stroke="var(--navy)" stroke-width="1.8"><circle cx="12" cy="12" r="10"/><ellipse cx="12" cy="12" rx="4.5" ry="10"/><path d="M2 12h20M4 7h16M4 17h16"/></svg>
        www.theharborcrestline.com
      </li>
    </ul>
  </section>

  <section class="card card--back" aria-label="Business card back">
    <div class="brand">
      <span class="brand__mark"></span>
      <span class="brand__name">Harbor Crestline</span>
    </div>
  </section>
</main>
</body>
</html>
```